Business Card Design Project

I require a business card with the following information on them for various different people;
name
m:
f:
e:
I have a logo already and will attached that. We are in the construction industry. I require something clean and simple but eye catching at the same time. You can use another colour with our logo if you like and you can style the logo as well if you wish. I am open.
Also it needs to be front and back design.
Industry/Entity Type
Construction
Requirements
Must have
- Logo, name, mobile, fax and email address.
Front and back design

```html
<!DOCTYPE html>
<html lang="en">
<head>
<meta charset="utf-8">
<title>Stonebridge Builders – Business Card</title>
<link rel="stylesheet" href="https://fonts.googleapis.com/css2?family=Open+Sans:wght@400;700&display=swap">
<style>
  :root {
    --backdrop: #a8872c;
    --card: #fbfaf7;
    --green: #5fb33b;
    --green-line: #6cbb4a;
    --ink: #2b2b2b;
  }
  * { margin: 0; padding: 0; box-sizing: border-box; }
  html, body { width: 1200px; height: 686px; overflow: hidden; }
  body {
    background: var(--backdrop);
    font-family: "Open Sans", Arial, sans-serif;
    position: relative;
  }
  .card {
    position: absolute;
    width: 523px;
    height: 299px;
    background: var(--card);
  }
  .card--front { left: 62px; top: 97px; }
  .card--back { left: 615px; top: 287px; }

  .rule {
    position: absolute;
    top: 142px;
    height: 2px;
    background: var(--green-line);
  }
  .rule--left { left: 0; width: 26px; }
  .rule--middle { left: 290px; width: 173px; }
  .rule--right { left: 493px; width: 30px; }

  .brand {
    position: absolute;
    display: flex;
    align-items: center;
    color: var(--green);
    font-weight: 400;
    white-space: nowrap;
  }
  .brand__mark { background: var(--green); flex: none; }
  .card--front .brand { left: 40px; top: 121px; font-size: 21px; gap: 8px; }
  .card--front .brand__mark { width: 22px; height: 22px; }
  .card--back .brand { left: 0; right: 0; top: 121px; justify-content: center; font-size: 38px; gap: 14px; }
  .card--back .brand__mark { width: 40px; height: 40px; }

  .holder-name {
    position: absolute;
    right: 61px;
    top: 103px;
    font-size: 17px;
    font-weight: 700;
    color: var(--green);
  }
  .contacts {
    position: absolute;
    right: 60px;
    top: 160px;
    list-style: none;
    text-align: right;
    font-size: 12px;
    color: var(--ink);
    line-height: 19.5px;
  }
  .contacts li { display: flex; justify-content: flex-end; align-items: center; gap: 6px; }
  .contacts svg { width: 12px; height: 12px; fill: var(--green); flex: none; }
</style>
</head>
<body>
  <section class="card card--front" aria-label="Card front">
    <div class="rule rule--left"></div>
    <div class="rule rule--middle"></div>
    <div class="rule rule--right"></div>
    <div class="brand"><span class="brand__mark"></span>Stonebridge Builders</div>
    <h1 class="holder-name">Your Name</h1>
    <ul class="contacts">
      <li>123-456-7890
        <svg viewBox="0 0 12 12" aria-hidden="true"><path d="M1 6c0-3 2.5-4.5 5-4.5S11 3 11 6l-2.2.4-.4-1.6C7.6 4.3 4.4 4.3 3.6 4.8l-.4 1.6z"/></svg></li>
      <li>123-456-7890
        <svg viewBox="0 0 12 12" aria-hidden="true"><path d="M3 1h5l1.5 1.5V5H3zM1 5.5h10v4.5H1zM2.5 7h7v1h-7z"/></svg></li>
      <li>name@website.com
        <svg viewBox="0 0 12 12" aria-hidden="true"><path d="M1 2.5h10v1L6 6.5 1 3.5zM1 5l5 3 5-3v4.5H1z"/></svg></li>
    </ul>
  </section>

  <section class="card card--back" aria-label="Card back">
    <div class="brand"><span class="brand__mark"></span>Stonebridge Builders</div>
  </section>
</body>
</html>
```